Business Card Design Project

We are looking to redesign the logo, business card and stationary of one of our group companies - SOLARO SUPPLY HOUSE LLC.

The company specialises in industrial PVC and CPVC Piping systems. It is situated in the Middle East and the focus is purely in this region.

The logo work is already completed. The file is uploaded for the reference.

We are looking for a clean minimalistic design for the business card.

regards
Rohit
Updates

Hello Everyone!

Thanks for submitting your designs. 

Yet to find the right design. Probably the below links will give you guys some more idea on what we would like.

Minimalist design with some creativity.

Rohit

http://exampledesignfolio.com/inspiration/15-beautifully-minimal-business-cards

http://www.samplelayoutbase.com/2011/11/14/30-minimalist-business-card-design/

http://www.primepixelcraft.com/inspiration/minimal-business-cards/

Target Market(s)

Industrial users

Industry/Entity Type

Industrial

Requirements
Must have
• - Minimalistic design

- Back side of the card should include the manufacturer PIPEMARQ NORTHERN's decal. The file is upload for the reference

- Further information
Company Name:
SOLARO SUPPLY HOUSE LLC
Address:
PO Box 8152, Sharjah Industrial Area 4, Qarwan Road
Sharjah, United Arab Emirates
Telephone:
+971-6-5000-118
Fax:
+977-6-5000-119
Email:
mail@sshlexample.com

- FYI, Solaro Supply House LLC is the authorised distributor for PIPEMARQ NORTHERN in the UAE. For further information on pipemarq please visit the website www.pipemarq-example.ca

```html
<!DOCTYPE html>
<html lang="en">
<head>
<meta charset="utf-8">
<title>Solaro Supply House LLC — Business Card</title>
<link rel="stylesheet" href="https://fonts.googleapis.com/css2?family=Arimo:wght@400;700&display=swap">
<style>
  :root {
    --card-bg: #f3f4f6;
    --fitting-light: #f9fafb;
    --fitting-tone: #dcdfe3;
    --fitting-deep: #c9cdd2;
    --brand-blue: #3a80cc;
    --phone-blue: #1f5cae;
    --mail-blue: #2e7bd0;
    --address-grey: #5a5a5a;
    --mark-dark: #1d2a36;
  }
  * { margin: 0; padding: 0; box-sizing: border-box; }
  html, body {
    width: 1200px;
    height: 686px;
    overflow: hidden;
    background: var(--card-bg);
  }
  .card {
    position: relative;
    width: 1200px;
    height: 686px;
    overflow: hidden;
    font-family: "Arimo", Arial, sans-serif;
    background: var(--card-bg);
  }
  .card__fitting-art {
    position: absolute;
    inset: 0;
    background:
      radial-gradient(ellipse 420px 380px at 920px 400px, var(--fitting-deep) 0%, var(--fitting-tone) 45%, transparent 75%),
      radial-gradient(ellipse 300px 230px at 260px 590px, var(--fitting-tone) 0%, transparent 70%),
      radial-gradient(ellipse 360px 200px at 600px 120px, var(--fitting-tone) 0%, transparent 70%),
      linear-gradient(135deg, var(--fitting-light) 0%, var(--card-bg) 55%, var(--fitting-tone) 100%);
    opacity: 0.85;
  }
  .card__top-rule {
    position: absolute;
    left: 0; top: 0;
    width: 100%; height: 5px;
    background: #e6e8eb;
  }
  .company-name {
    position: absolute;
    left: 49px;
    top: 108px;
    width: 494px;
    text-align: center;
    font-weight: 700;
    font-size: 52px;
    line-height: 64px;
    letter-spacing: 0.5px;
    color: var(--brand-blue);
    text-shadow: 3px 4px 6px rgba(0, 0, 0, 0.28);
  }
  .address {
    position: absolute;
    left: 49px;
    top: 248px;
    font-weight: 700;
    font-size: 25px;
    line-height: 34.3px;
    color: var(--address-grey);
    font-style: normal;
  }
  .phones {
    position: absolute;
    left: 49px;
    top: 424px;
    font-weight: 700;
    font-size: 29px;
    line-height: 40px;
    color: var(--phone-blue);
    list-style: none;
  }
  .brand-mark {
    position: absolute;
    left: 0;
    width: 100%;
    top: 540px;
    display: flex;
    justify-content: center;
    align-items: center;
    gap: 12px;
  }
  .brand-mark__square {
    width: 54px;
    height: 54px;
    border-radius: 12px;
    background: var(--mark-dark);
  }
  .brand-mark__name {
    font-weight: 700;
    font-size: 22px;
    color: var(--brand-blue);
  }
  .email {
    position: absolute;
    left: 0;
    width: 100%;
    top: 628px;
    text-align: center;
    font-weight: 700;
    font-size: 25px;
    color: var(--mail-blue);
  }
</style>
</head>
<body>
  <main class="card">
    <div class="card__fitting-art" role="img" aria-label="Faint background illustration of PVC pipe fittings"></div>
    <div class="card__top-rule"></div>

    <h1 class="company-name">SOLARO SUPPLY<br>HOUSE LLC</h1>

    <address class="address">
      PO Box 8152<br>
      Sharjah Industrial Area 4<br>
      Qarwan Road<br>
      Sharjah<br>
      United Arab Emirates
    </address>

    <ul class="phones">
      <li>+971-6-5000-118</li>
      <li>+977-6-5000-119</li>
    </ul>

    <div class="brand-mark">
      <span class="brand-mark__square"></span>
      <span class="brand-mark__name">SOLARO</span>
    </div>

    <p class="email">mail@sshlexample.com</p>
  </main>
</body>
</html>
```